Business Card and Simple Logo Desgin

New Zealand based start up company "Vesta Advisory LTD" requires business cards and simple logo design.

Card Content.

Vesta Advisory LTD

Rebecca Thornbury
CA, BMS (Hons)

r.thornbury@vestaadvisory.co.nz
PH +64 21 574 613

Target Market(s)

Corporate Business in IT, Finance and accounting.

Industry/Entity Type

Business

```html
<!DOCTYPE html>
<html lang="en">
<head>
<meta charset="utf-8">
<title>Vesta Advisory LTD — Business Card</title>
<link rel="stylesheet" href="https://fonts.googleapis.com/css2?family=Oswald:wght@400;500&display=swap">
<style>
  :root {
    --backdrop: #ffffff;
    --card: #f4f4f4;
    --brand-purple: #6f2a8e;
    --ink: #1d1a1b;
    --band: #5c3a72;
    --on-dark: #ffffff;
  }
  html, body {
    margin: 0;
    padding: 0;
    width: 900px;
    height: 1200px;
    overflow: hidden;
    background: var(--backdrop);
  }
  .canvas {
    position: relative;
    width: 900px;
    height: 1200px;
    font-family: "Oswald", "Arial Narrow", sans-serif;
  }
  .card {
    position: absolute;
    left: 152px;
    top: 108px;
    width: 576px;
    height: 1007px;
    background: var(--card);
    overflow: hidden;
  }
  .brand-name {
    position: absolute;
    left: 176px;
    top: 96px;
    margin: 0;
    font-weight: 500;
    font-size: 80px;
    line-height: 80px;
    letter-spacing: 0.5px;
    color: var(--brand-purple);
    text-transform: uppercase;
  }
  .brand-name span { display: block; }
  .holder {
    position: absolute;
    left: 78px;
    top: 470px;
  }
  .holder-name {
    margin: 0;
    font-weight: 500;
    font-size: 47px;
    line-height: 56px;
    letter-spacing: 0.5px;
    color: var(--ink);
    text-transform: uppercase;
  }
  .holder-credentials {
    margin: 4px 0 0 1px;
    font-weight: 500;
    font-size: 17px;
    letter-spacing: 0.8px;
    color: var(--ink);
  }
  .contact-band {
    position: absolute;
    left: 143px;
    top: 715px;
    right: 0;
    bottom: 0;
    background: var(--band);
  }
  .contact {
    position: absolute;
    left: 175px;
    top: 760px;
    color: var(--on-dark);
  }
  .contact-email {
    margin: 0;
    font-size: 29px;
    line-height: 40px;
    font-weight: 400;
  }
  .contact-phone {
    margin: 4px 0 0;
    font-size: 31px;
    line-height: 40px;
    font-weight: 400;
  }
  .contact-phone .label {
    font-size: 16px;
    margin-right: 10px;
  }
</style>
</head>
<body>
<main class="canvas">
  <section class="card" aria-label="Business card for Vesta Advisory LTD">
    <h1 class="brand-name"><span>Vesta</span><span>Advisory</span><span>LTD</span></h1>

    <div class="holder">
      <h2 class="holder-name">Rebecca Thornbury</h2>
      <p class="holder-credentials">CA, BMS (HONS)</p>
    </div>

    <div class="contact-band"></div>

    <div class="contact">
      <p class="contact-email">r.thornbury@vestaadvisory.co.nz</p>
      <p class="contact-phone"><span class="label">Tel</span>+64 21 574 613</p>
    </div>
  </section>
</main>
</body>
</html>
```